Company or website name
- Quiet Hollow Properties
- Describe your company and organization and target audience
- We sell rural vacant, mostly residential land. Our target market is looking for privacy and either a place to retire to or a place to escape to.
- The design should have the following
- Mountains, Pine Trees, Earthy Colors, and match the attached logo. The home page should have designs for slides of properties at the top, followed by a survey (for users to share details of the property they're looking for), followed by search functionality, individual properties and general areas properties are available in. We'll also need at least one contact form on each page as well as maps. For the property detail page we'll need a large area for pictures, highlighted property details, a description and more detailed facts about property. The property detail page should also have a survey for users to share details of what they're looking for and contact form. Last but not least, similar properties should also be included on the property listing page. The winning design will include an excellent "Contact Us" page! Every page should have an opt-in offering users to be notified when new properties become available.
- Briefly describe your contest

```html
<!DOCTYPE html>
<html lang="en">
<head>
<meta charset="utf-8">
<title>Quiet Hollow Properties – Page Designs</title>
<link href="https://fonts.googleapis.com/css2?family=Montserrat:wght@400;500;600;700&display=swap" rel="stylesheet">
<style>
:root{
  --green:#6a8763;
  --green-dark:#4f6a48;
  --footer:#4b4f52;
  --grey-bg:#efefef;
  --grey-line:#9a9a9a;
  --ink:#333638;
  --muted:#7a7d80;
  --white:#ffffff;
  --card-bar:#8d8f91;
}
*{box-sizing:border-box;margin:0;padding:0}
html,body{width:1061px;height:1200px;overflow:hidden;background:var(--white)}
body{position:relative;font-family:"Montserrat",Arial,sans-serif;color:var(--ink)}

.page{position:absolute;top:31px;width:313px;background:var(--white);box-shadow:0 0 4px rgba(0,0,0,.12)}
.page--home{left:36px}
.page--property{left:375px}
.page--contact{left:714px}
.section{position:relative;overflow:visible}
.abs{position:absolute}

/* header */
.site-header{height:28px;background:var(--white);position:relative;z-index:3}
.nav{position:absolute;top:17px;right:32px;display:flex;gap:7px;align-items:center;font-size:2.6px;letter-spacing:.2px;color:var(--muted)}
.nav .account{width:5px;height:5px;border-radius:50%;background:var(--muted)}
.brand-badge{position:absolute;left:33px;top:6px;width:40px;height:40px;border-radius:50%;background:var(--white);box-shadow:0 0 3px rgba(0,0,0,.25);display:flex;align-items:center;justify-content:center;text-align:center;font-size:4.2px;font-weight:700;line-height:1.15;color:var(--ink);z-index:4}

/* photo fills */
.ph-lake{background:linear-gradient(180deg,#6fa6dd 0%,#bcd7ef 35%,#2f5c36 52%,#3d77a8 68%,#5f8a3a 100%)}
.ph-sunset{background:linear-gradient(180deg,#2c3c6b 0%,#b3597a 40%,#e0915a 55%,#3a4d78 75%,#1f2b47 100%)}
.ph-fields{background:linear-gradient(180deg,#9bbf5c 0%,#5f8f2e 45%,#8cb64a 70%,#4e7a25 100%)}
.ph-wheat{background:linear-gradient(180deg,#2f6fc8 0%,#a9c9ee 45%,#8a5e3c 62%,#6e4a2e 100%)}
.ph-mountain{background:linear-gradient(180deg,#7da4c9 0%,#c5d6e3 35%,#5b6d78 55%,#33452f 100%)}
.ph-valley{background:linear-gradient(180deg,#e9e6d2 0%,#b6b58a 35%,#7d8a45 65%,#5a6a2e 100%)}
.ph-hero{background:linear-gradient(180deg,#5d6f7b 0%,#8b99a0 30%,#55636a 55%,#2d3a2b 80%,#1f2a1d 100%)}
.ph-keys{background:linear-gradient(90deg,#dcdcdc 0%,#eeeeee 40%,#e8e8e8 100%)}
.ph-map{background:linear-gradient(135deg,#eef0ea 0%,#e3e8dc 50%,#eceee6 100%)}

/* hero */
.hero{height:120px}
.hero-title{position:absolute;top:27px;width:100%;text-align:center;font-size:13px;font-weight:700;color:var(--white)}
.hero-text{position:absolute;top:48px;left:76px;width:161px;text-align:center;font-size:3.4px;line-height:1.45;color:var(--white)}
.search{position:absolute;left:82px;top:73px;width:148px;height:11px;border-radius:6px;background:var(--white);font-size:3.2px;color:var(--muted);padding-left:7px;line-height:11px}
.search::after{content:"";position:absolute;right:6px;top:3.5px;width:3px;height:3px;border:0.6px solid var(--muted);border-radius:50%}

/* headings */
.heading{position:absolute;width:100%;text-align:center;font-size:9px;font-weight:600;color:var(--ink)}
.heading::after{content:"";position:absolute;left:50%;margin-left:-14.5px;top:13px;width:29px;height:1px;background:var(--grey-line)}
.heading--light{color:var(--white)}
.heading--light::after{background:rgba(255,255,255,.7)}
.lead{position:absolute;width:100%;text-align:center;font-size:3.4px;line-height:1.5;color:var(--ink)}

/* listing cards */
.featured{height:220px}
.listing{position:absolute;width:54px;height:59px;background:var(--white);box-shadow:0 0 2px rgba(0,0,0,.18)}
.listing .photo{position:absolute;left:2px;top:2px;width:50px;height:35px}
.listing .name{position:absolute;left:2px;top:38.5px;font-size:2.4px;font-weight:600}
.listing .sub{position:absolute;left:2px;top:41.5px;font-size:1.8px;color:var(--muted)}
.listing .price{position:absolute;left:2px;top:45px;font-size:4.2px;font-weight:700}
.listing .bar{position:absolute;left:0;bottom:0;width:100%;height:4.5px;background:var(--card-bar);font-size:1.8px;color:var(--white);padding-left:3px;line-height:4.5px}
.listing .bar i{position:absolute;top:1.3px;width:2px;height:2px;border:0.4px solid var(--white);border-radius:50%}
.btn-outline{position:absolute;left:127px;top:192px;width:59px;height:9px;border:0.6px solid var(--grey-line);border-radius:5px;font-size:2.6px;text-align:center;line-height:8px;color:var(--muted)}

/* forms */
.field{position:absolute;height:9px;background:var(--white);border-radius:5px;box-shadow:0 0 1.5px rgba(0,0,0,.2);font-size:2.4px;color:var(--muted);padding-left:5px;line-height:9px}
.field--area{height:35px;border-radius:3px;line-height:1;padding-top:5px}
.btn{position:absolute;height:9px;width:59px;background:var(--green-dark);border-radius:5px;font-size:2.5px;color:var(--white);text-align:center;line-height:9px}

.survey{height:147px}
.survey .backdrop{position:absolute;inset:0}

/* communities */
.communities{height:125px}
.community{position:absolute;top:47px;width:50px;height:49px}
.community-label{position:absolute;top:102px;width:50px;text-align:center;font-size:3.2px;color:var(--ink)}
.arrow{position:absolute;width:5px;height:5px;border:0.6px solid var(--grey-line);border-radius:50%}
.arrow::after{content:"";position:absolute;left:1.3px;top:1.4px;width:1.4px;height:1.4px;border-left:0.6px solid var(--grey-line);border-bottom:0.6px solid var(--grey-line);transform:rotate(45deg)}
.arrow--next::after{transform:rotate(-135deg);left:0.9px}

/* contact */
.contact{height:var(--h)}
.contact .band{position:absolute;left:0;top:var(--band-top);width:100%;height:var(--band-h);background:var(--green)}
.contact .heading{top:var(--title)}
.contact .lead{top:var(--sub);color:var(--white)}
.contact-card{position:absolute;left:50px;top:var(--card);width:213px;height:96px;background:var(--white);box-shadow:0 0 3px rgba(0,0,0,.18)}
.contact-card .aside{position:absolute;right:0;top:0;width:78px;height:100%;background:var(--grey-bg)}
.contact-card .aside p{position:absolute;left:9px;font-size:2.7px;color:var(--muted)}
.contact-card .aside .strong{font-weight:600;color:var(--ink)}
.contact--home{--h:160px;--band-top:0px;--band-h:94px;--title:16px;--sub:36px;--card:48px}
.contact--property{--h:176px;--band-top:17px;--band-h:94px;--title:33px;--sub:53px;--card:65px}
.contact--page{--h:176px;--band-top:0px;--band-h:110px;--title:31px;--sub:52px;--card:64px}

/* map + footer */
.map{height:77px}
.site-footer{height:86px;background:var(--footer);text-align:center;color:var(--white)}
.site-footer .brand-badge{left:140px;top:-12px;width:33px;height:33px;font-size:3.4px}
.signup-title{position:absolute;top:29px;width:100%;font-size:4.4px;font-weight:600}
.signup-field{position:absolute;left:104px;top:37px;width:105px;height:10px;border-radius:5px;background:var(--white);font-size:2.8px;color:var(--muted);text-align:left;padding-left:7px;line-height:10px}
.signup-field::after{content:"";position:absolute;right:4px;top:3px;width:4px;height:4px;border:0.5px solid var(--grey-line);border-radius:50%}
.footer-links{position:absolute;top:58px;width:100%;font-size:3.4px}
.footer-legal{position:absolute;top:68px;width:100%;font-size:2.6px}

/* property page */
.crumbs{position:absolute;top:12px;width:100%;text-align:center;font-size:2.8px;color:var(--muted)}
.title-area{height:53px}
.title-area .heading{top:24px}
.gallery{height:137px}
.thumbs{height:45px}
.thumb{position:absolute;top:5px;width:51px;height:35px}
.details{height:258px;background:var(--grey-bg)}
.tools{position:absolute;left:234px;top:9px;display:flex;gap:3px}
.tools i{width:3.5px;height:3.5px;border:0.5px solid var(--grey-line);border-radius:50%}
.detail-card{position:absolute;left:32px;top:19px;width:239px;height:209px;background:var(--white);padding:9px 10px;overflow:hidden}
.detail-card h2{font-size:5px;font-weight:600;margin-bottom:5px}
.detail-card .addr{font-size:3.6px;margin-bottom:4px}
.detail-card .price{font-size:7.5px;font-weight:700;color:var(--green-dark);margin-bottom:6px}
.detail-card .price small{font-size:2.4px;color:var(--ink);font-weight:600}
.detail-card h3{font-size:4.8px;font-weight:600;margin-bottom:1px}
.detail-card p{font-size:2.9px;line-height:1.58;color:#555;margin-bottom:5px}
.scrollbar{position:absolute;left:274px;top:19px;width:2.5px;height:209px;background:#e2e2e2}
.scrollbar::after{content:"";position:absolute;left:0.7px;top:10px;width:1.1px;height:60px;background:#b5b5b5}
.similar{height:127px}
.similar .community{top:48px}
.similar .community-label{top:103px}
</style>
</head>
<body>

<!-- HOME PAGE -->
<div class="page page--home">
  <header class="site-header">
    <div class="brand-badge">Quiet<br>Hollow</div>
    <nav class="nav"><span>HOME</span><span>ABOUT</span><span>PROPERTIES</span><span>CONTACT</span><span class="account"></span></nav>
  </header>

  <section class="section hero ph-hero" role="img" aria-label="Mountain valley with pine forest">
    <h1 class="hero-title">Freedom Awaits</h1>
    <p class="hero-text">Lorem ipsum dolor sit amet, consectetur adipiscing elit. Ut mollis vestibulum odio, ac pellentesque arcu posuere et. Aenean dignissim leo eu ipsum mattis, ac viverra ante malesuada. Nulla eu lacinia elit. Etiam vitae iaculis nunc.</p>
    <div class="search">Find your Quiet Hollow property...</div>
  </section>

  <section class="section featured">
    <h2 class="heading" style="top:19px">Featured Listings</h2>
    <div class="listing" style="left:36px;top:51px"><div class="photo ph-lake" role="img" aria-label="Lake property photo"></div><div class="name">Mountainside Lake Property</div><div class="sub">Lorem ipsum dolor sit amet</div><div class="price">$299,999</div><div class="bar">View Property Details<i style="right:10px"></i><i style="right:6px"></i><i style="right:2px"></i></div></div>
    <div class="listing" style="left:98px;top:51px"><div class="photo ph-sunset" role="img" aria-label="Sunset over hills photo"></div><div class="name">Mountainside Lake Property</div><div class="sub">Lorem ipsum dolor sit amet</div><div class="price">$299,999</div><div class="bar">View Property Details<i style="right:10px"></i><i style="right:6px"></i><i style="right:2px"></i></div></div>
    <div class="listing" style="left:160px;top:51px"><div class="photo ph-fields" role="img" aria-label="Green fields photo"></div><div class="name">Mountainside Lake Property</div><div class="sub">Lorem ipsum dolor sit amet</div><div class="price">$299,999</div><div class="bar">View Property Details<i style="right:10px"></i><i style="right:6px"></i><i style="right:2px"></i></div></div>
    <div class="listing" style="left:222px;top:51px"><div class="photo ph-wheat" role="img" aria-label="Open farmland photo"></div><div class="name">Mountainside Lake Property</div><div class="sub">Lorem ipsum dolor sit amet</div><div class="price">$299,999</div><div class="bar">View Property Details<i style="right:10px"></i><i style="right:6px"></i><i style="right:2px"></i></div></div>
    <div class="listing" style="left:36px;top:119px"><div class="photo ph-lake" role="img" aria-label="Lake property photo"></div><div class="name">Mountainside Lake Property</div><div class="sub">Lorem ipsum dolor sit amet</div><div class="price">$299,999</div><div class="bar">View Property Details<i style="right:10px"></i><i style="right:6px"></i><i style="right:2px"></i></div></div>
    <div class="listing" style="left:98px;top:119px"><div class="photo ph-sunset" role="img" aria-label="Sunset over hills photo"></div><div class="name">Mountainside Lake Property</div><div class="sub">Lorem ipsum dolor sit amet</div><div class="price">$299,999</div><div class="bar">View Property Details<i style="right:10px"></i><i style="right:6px"></i><i style="right:2px"></i></div></div>
    <div class="listing" style="left:160px;top:119px"><div class="photo ph-fields" role="img" aria-label="Green fields photo"></div><div class="name">Mountainside Lake Property</div><div class="sub">Lorem ipsum dolor sit amet</div><div class="price">$299,999</div><div class="bar">View Property Details<i style="right:10px"></i><i style="right:6px"></i><i style="right:2px"></i></div></div>
    <div class="listing" style="left:222px;top:119px"><div class="photo ph-wheat" role="img" aria-label="Open farmland photo"></div><div class="name">Mountainside Lake Property</div><div class="sub">Lorem ipsum dolor sit amet</div><div class="price">$299,999</div><div class="bar">View Property Details<i style="right:10px"></i><i style="right:6px"></i><i style="right:2px"></i></div></div>
    <div class="btn-outline">View All Listings</div>
  </section>

  <section class="section survey">
    <div class="backdrop ph-keys" role="img" aria-label="House keys in a door lock, faded"></div>
    <h2 class="heading" style="top:13px">What are you looking for?</h2>
    <p class="lead" style="top:34px;left:76px;width:161px">Can't find what you are looking for? Fill out the form below to tell us what kind of property you want, and we'll let you know if something becomes available.</p>
    <div class="field" style="left:100px;top:53px;width:53px">First Name</div>
    <div class="field" style="left:159px;top:53px;width:53px">Last Name</div>
    <div class="field" style="left:100px;top:68px;width:112px">Email Address</div>
    <div class="field field--area" style="left:100px;top:83px;width:112px">Tell us what you are looking for...</div>
    <div class="btn" style="left:127px;top:125px">Submit Your Form</div>
  </section>

  <section class="section communities">
    <h2 class="heading" style="top:17px">Browse Communities</h2>
    <span class="arrow" style="left:39px;top:69px"></span>
    <div class="community ph-lake" style="left:50px" role="img" aria-label="Lake community"></div>
    <div class="community ph-mountain" style="left:104px" role="img" aria-label="Mountain community"></div>
    <div class="community ph-valley" style="left:158px" role="img" aria-label="Valley farmland community"></div>
    <div class="community ph-wheat" style="left:212px" role="img" aria-label="Plains community"></div>
    <span class="arrow arrow--next" style="left:269px;top:69px"></span>
    <p class="community-label" style="left:50px">City Name, State</p>
    <p class="community-label" style="left:104px">City Name, State</p>
    <p class="community-label" style="left:158px">City Name, State</p>
    <p class="community-label" style="left:212px">City Name, State</p>
  </section>

  <section class="section contact contact--home">
    <div class="band"></div>
    <h2 class="heading heading--light">Get in Touch</h2>
    <p class="lead">Have questions? We would love to hear from you.</p>
    <div class="contact-card">
      <div class="field" style="left:12px;top:8px;width:53px">First Name</div>
      <div class="field" style="left:70px;top:8px;width:53px">Last Name</div>
      <div class="field" style="left:12px;top:22px;width:111px">Email Address</div>
      <div class="field field--area" style="left:12px;top:38px;width:111px">How can we help you?</div>
      <div class="btn" style="left:39px;top:78px">Submit Your Form</div>
      <div class="aside"><p class="strong" style="top:9px">Quiet Hollow Properties</p><p style="top:17px">Street Address</p><p style="top:25px">City, State Zip</p><p class="strong" style="top:40px">555-555-5555</p><p class="strong" style="top:48px">info@emailaddress.com</p></div>
    </div>
  </section>

  <section class="section map ph-map" role="img" aria-label="Road map of the regions with available land"></section>

  <footer class="section site-footer">
    <div class="brand-badge">Quiet<br>Hollow</div>
    <p class="signup-title">Sign Up for to Hear About New Listings</p>
    <div class="signup-field">Enter your email address</div>
    <p class="footer-links">Properties | Features | Blog | Contact</p>
    <p class="footer-legal">© 2022 Quiet Hollow Properties | Terms of Service | Privacy Notice</p>
  </footer>
</div>

<!-- PROPERTY PAGE -->
<div class="page page--property">
  <header class="site-header">
    <div class="brand-badge">Quiet<br>Hollow</div>
    <nav class="nav"><span>HOME</span><span>ABOUT</span><span>PROPERTIES</span><span>CONTACT</span><span class="account"></span></nav>
  </header>

  <section class="section title-area">
    <p class="crumbs">Home / Properties / Mountainside Lake Property</p>
    <h1 class="heading">Mountainside Lake Property</h1>
  </section>

  <section class="section gallery ph-lake" role="img" aria-label="Lake with pine forest and grassy shore"></section>

  <section class="section thumbs">
    <span class="arrow" style="left:39px;top:20px"></span>
    <div class="thumb ph-mountain" style="left:49px" role="img" aria-label="Mountain view"></div>
    <div class="thumb ph-fields" style="left:103px" role="img" aria-label="Green fields"></div>
    <div class="thumb ph-wheat" style="left:157px" role="img" aria-label="Open farmland"></div>
    <div class="thumb ph-sunset" style="left:211px" role="img" aria-label="Sunset over hills"></div>
    <span class="arrow arrow--next" style="left:269px;top:20px"></span>
  </section>

  <section class="section details">
    <div class="tools"><i></i><i></i><i></i><i></i></div>
    <article class="detail-card">
      <h2>Mountainside Lake Property</h2>
      <p class="addr">Street Address, City, State Zip</p>
      <p class="price">$299,999 <small>Est. Monthly $1400</small></p>
      <h3>Details</h3>
      <p>Lorem ipsum dolor sit amet, consectetur adipiscing elit. Suspendisse pellentesque laoreet erat, condimentum aliquet tellus aliquam sit amet. Quisque ultricies nibh at blandit sollicitudin. Suspendisse faucibus sollicitudin mauris, ut sollicitudin arcu venenatis nec. Praesent placerat auctor ultrices. Etiam mollis tortor sed congue iaculis. Donec non euismod nibh. Nullam eu bibendum dui.</p>
      <p>In hac habitasse platea dictumst. Praesent mattis condimentum egestas. Pellentesque tempor consequat dolor at ultrices. Praesent blandit, nisi at cursus semper, justo mi pretium tortor, ac blandit nisi lacus eu augue. Proin quis interdum est, sed blandit lectus. Nunc posuere, erat quis dictum malesuada, quam magna pellentesque leo, vel dapibus risus felis in tortor. Etiam non felis volutpat nisi imperdiet facilisis non id odio. Nam fringilla turpis nunc, sit amet rhoncus sem viverra sit amet. Nam scelerisque vitae nisl venenatis venenatis.</p>
      <h3>About the Community</h3>
      <p>Lorem ipsum dolor sit amet, consectetur adipiscing elit. Suspendisse pellentesque laoreet erat, condimentum aliquet tellus aliquam sit amet. Quisque ultricies nibh at blandit sollicitudin. Suspendisse faucibus sollicitudin mauris, ut sollicitudin arcu venenatis nec. Praesent placerat auctor ultrices. Etiam mollis tortor sed congue iaculis. Donec non euismod nibh. Nullam eu bibendum dui.</p>
      <p>In hac habitasse platea dictumst. Praesent mattis condimentum egestas. Pellentesque tempor consequat dolor at ultrices. Praesent blandit, nisi at cursus semper, justo mi pretium tortor, ac blandit nisi lacus eu augue. Proin quis interdum est, sed blandit lectus. Nunc posuere, erat quis dictum malesuada, quam magna pellentesque leo, vel dapibus risus felis in tortor. Etiam non felis volutpat nisi imperdiet facilisis non id odio. Nam fringilla turpis nunc, sit amet rhoncus sem viverra sit amet. Nam scelerisque vitae nisl venenatis venenatis.</p>
    </article>
    <div class="scrollbar"></div>
    <div class="btn" style="left:94px;top:236px">Contact Us</div>
    <div class="btn" style="left:159px;top:236px">Schedule a Tour</div>
  </section>

  <section class="section similar communities">
    <h2 class="heading" style="top:19px">Similar Listings</h2>
    <span class="arrow" style="left:39px;top:70px"></span>
    <div class="community ph-lake" style="left:49px;width:51px" role="img" aria-label="Lake property"></div>
    <div class="community ph-mountain" style="left:103px;width:51px" role="img" aria-label="Mountain property"></div>
    <div class="community ph-valley" style="left:157px;width:51px" role="img" aria-label="Valley farmland property"></div>
    <div class="community ph-wheat" style="left:211px;width:51px" role="img" aria-label="Plains property"></div>
    <span class="arrow arrow--next" style="left:269px;top:70px"></span>
    <p class="community-label" style="left:49px">City Name, State</p>
    <p class="community-label" style="left:103px">City Name, State</p>
    <p class="community-label" style="left:157px">City Name, State</p>
    <p class="community-label" style="left:211px">City Name, State</p>
  </section>

  <section class="section survey">
    <div class="backdrop ph-keys" role="img" aria-label="House keys in a door lock, faded"></div>
    <h2 class="heading" style="top:13px">What are you looking for?</h2>
    <p class="lead" style="top:34px;left:76px;width:161px">Can't find what you are looking for? Fill out the form below to tell us what kind of property you want, and we'll let you know if something becomes available.</p>
    <div class="field" style="left:100px;top:53px;width:53px">First Name</div>
    <div class="field" style="left:159px;top:53px;width:53px">Last Name</div>
    <div class="field" style="left:100px;top:68px;width:112px">Email Address</div>
    <div class="field field--area" style="left:100px;top:83px;width:112px">Tell us what you are looking for...</div>
    <div class="btn" style="left:127px;top:125px">Submit Your Form</div>
  </section>

  <section class="section contact contact--property">
    <div class="band"></div>
    <h2 class="heading heading--light">Get in Touch</h2>
    <p class="lead">Have questions? We would love to hear from you.</p>
    <div class="contact-card">
      <div class="field" style="left:12px;top:8px;width:53px">First Name</div>
      <div class="field" style="left:70px;top:8px;width:53px">Last Name</div>
      <div class="field" style="left:12px;top:22px;width:111px">Email Address</div>
      <div class="field field--area" style="left:12px;top:38px;width:111px">How can we help you?</div>
      <div class="btn" style="left:39px;top:78px">Submit Your Form</div>
      <div class="aside"><p class="strong" style="top:9px">Quiet Hollow Properties</p><p style="top:17px">Street Address</p><p style="top:25px">City, State Zip</p><p class="strong" style="top:40px">555-555-5555</p><p class="strong" style="top:48px">info@emailaddress.com</p></div>
    </div>
  </section>

  <section class="section map ph-map" role="img" aria-label="Road map of the regions with available land"></section>

  <footer class="section site-footer">
    <div class="brand-badge">Quiet<br>Hollow</div>
    <p class="signup-title">Sign Up for to Hear About New Listings</p>
    <div class="signup-field">Enter your email address</div>
    <p class="footer-links">Properties | Features | Blog | Contact</p>
    <p class="footer-legal">© 2022 Quiet Hollow Properties | Terms of Service | Privacy Notice</p>
  </footer>
</div>

<!-- CONTACT PAGE -->
<div class="page page--contact">
  <header class="site-header">
    <div class="brand-badge">Quiet<br>Hollow</div>
    <nav class="nav"><span>HOME</span><span>ABOUT</span><span>PROPERTIES</span><span>CONTACT</span><span class="account"></span></nav>
  </header>

  <section class="section contact contact--page">
    <div class="band"></div>
    <h1 class="heading heading--light">Get in Touch</h1>
    <p class="lead">Have questions? We would love to hear from you.</p>
    <div class="contact-card">
      <div class="field" style="left:12px;top:8px;width:53px">First Name</div>
      <div class="field" style="left:70px;top:8px;width:53px">Last Name</div>
      <div class="field" style="left:12px;top:22px;width:111px">Email Address</div>
      <div class="field field--area" style="left:12px;top:38px;width:111px">How can we help you?</div>
      <div class="btn" style="left:39px;top:78px">Submit Your Form</div>
      <div class="aside"><p class="strong" style="top:9px">Quiet Hollow Properties</p><p style="top:17px">Street Address</p><p style="top:25px">City, State Zip</p><p class="strong" style="top:40px">555-555-5555</p><p class="strong" style="top:48px">info@emailaddress.com</p></div>
    </div>
  </section>

  <section class="section map ph-map" role="img" aria-label="Road map of the regions with available land"></section>

  <footer class="section site-footer" style="height:85px">
    <div class="brand-badge">Quiet<br>Hollow</div>
    <p class="signup-title">Sign Up for to Hear About New Listings</p>
    <div class="signup-field">Enter your email address</div>
    <p class="footer-links">Properties | Features | Blog | Contact</p>
    <p class="footer-legal">© 2022 Quiet Hollow Properties | Terms of Service | Privacy Notice</p>
  </footer>
</div>

</body>
</html>
```